Structural Engineering Business Card

Brookvane Drafting does residential house plans for clients in Central Florida. Would like simple but elegant business card that is appropriate for a house plan engineering company. Prefer black business card with black/white them but open to other shades of blue. I uploaded a sample card that I came across that looked good but please come up with your own creative designs.

Contact Information for Business Card

Name, Title, Phone, Email, Address, website

```html
<!DOCTYPE html>
<html lang="en">
<head>
<meta charset="UTF-8">
<title>Brookvane Drafting – Business Card</title>
<link href="https://fonts.googleapis.com/css2?family=Montserrat:wght@300;400;600;800&display=swap" rel="stylesheet">
<style>
  :root {
    --backdrop: #b3b3b3;
    --card: #262626;
    --accent: #5bc4e2;
    --mark-grey: #8c8c8c;
    --mark-grey-back: #6f6f6f;
    --text-light: #e6e6e6;
    --text-muted: #bdbdbd;
  }
  * { box-sizing: border-box; margin: 0; padding: 0; }
  html, body {
    width: 1200px; height: 900px; overflow: hidden;
    background: var(--backdrop);
    font-family: "Montserrat", sans-serif;
  }
  .sheet {
    width: 1200px; height: 900px;
    display: flex; flex-direction: column; align-items: center; justify-content: center;
    gap: 40px;
  }
  .card {
    position: relative;
    width: 700px; height: 400px;
    background: var(--card);
    border-radius: 18px;
    overflow: hidden;
    box-shadow: 0 10px 24px rgba(0,0,0,.3);
  }

  /* Front */
  .brand-name {
    position: absolute; left: 60px; top: 54px;
    font-weight: 800; font-size: 50px; line-height: 1.02;
    letter-spacing: 1px; text-transform: uppercase;
    color: var(--mark-grey);
  }
  .person {
    position: absolute; left: 60px; top: 196px;
  }
  .person-name {
    font-weight: 600; font-size: 28px; color: var(--accent);
  }
  .person-title {
    font-weight: 300; font-size: 17px; color: var(--text-muted);
    text-align: right; margin-top: 2px;
  }
  .divider {
    position: absolute; left: 322px; top: 188px;
    width: 1.5px; height: 84px; background: var(--accent);
  }
  .contact-list {
    position: absolute; left: 346px; top: 188px;
    list-style: none;
    display: flex; flex-direction: column; gap: 11px;
  }
  .contact-item {
    display: flex; align-items: center; gap: 12px;
    font-weight: 400; font-size: 17px; color: var(--text-light);
  }
  .contact-icon { width: 16px; height: 16px; flex: none; }
  .address-band {
    position: absolute; left: 0; right: 0; top: 318px; height: 44px;
    background: var(--accent);
    display: flex; align-items: center; justify-content: center;
    font-weight: 400; font-size: 17px; color: #ffffff; letter-spacing: .3px;
  }

  /* Back */
  .card--back .brand-name {
    left: 0; right: 0; top: 50%; transform: translateY(-50%);
    text-align: center; font-size: 62px;
    color: var(--mark-grey-back);
  }
  .edge-line {
    position: absolute; left: 0; right: 0; bottom: 0; height: 7px;
    background: var(--accent);
  }
</style>
</head>
<body>
<main class="sheet">

  <section class="card card--front" aria-label="Business card front">
    <div class="brand-name">Brookvane<br>Drafting</div>

    <div class="person">
      <div class="person-name">Daniel Reyes</div>
      <div class="person-title">Owner</div>
    </div>

    <div class="divider"></div>

    <ul class="contact-list">
      <li class="contact-item">
        <svg class="contact-icon" viewBox="0 0 16 16" aria-hidden="true">
          <path fill="#5bc4e2" d="M3.6 1.5l2.2 2.6-1.3 1.6c.9 2 2.3 3.4 4.3 4.3l1.6-1.3 2.6 2.2-1.3 2.4C6.6 13.2 2.8 9.4 1.3 3.3z"/>
        </svg>
        +49 404 552 3180
      </li>
      <li class="contact-item">
        <svg class="contact-icon" viewBox="0 0 16 16" aria-hidden="true">
          <rect x="1" y="3" width="14" height="10" rx="1" fill="#5bc4e2"/>
          <path d="M1.5 3.8L8 9l6.5-5.2" fill="none" stroke="#262626" stroke-width="1.3"/>
        </svg>
        hello@brookvane.com
      </li>
      <li class="contact-item">
        <svg class="contact-icon" viewBox="0 0 16 16" aria-hidden="true">
          <circle cx="8" cy="8" r="6.5" fill="none" stroke="#5bc4e2" stroke-width="1.5"/>
          <ellipse cx="8" cy="8" rx="2.8" ry="6.5" fill="none" stroke="#5bc4e2" stroke-width="1.2"/>
          <path d="M1.5 8h13" stroke="#5bc4e2" stroke-width="1.2"/>
        </svg>
        www.brookvane.com
      </li>
    </ul>

    <div class="address-band">Lindenweg 42, 22769 Hamburg</div>
  </section>

  <section class="card card--back" aria-label="Business card back">
    <div class="brand-name">Brookvane Drafting</div>
    <div class="edge-line"></div>
  </section>

</main>
</body>
</html>
```